Willow Crest Brand - Bag Design

We are a company dealing with nuts, grains and seeds and are looking for a design for our retail bag packaging that will be consistent across all our product range. We are currently differentiating in way of color but please feel free to be more creative if you wish. Sample of products include pumpkin seeds, rolled oats, almonds, etc.
Design Idea: Hygienic, Natural (from Nature), Quality & Upscale, Simple & Clean design
Target Market: High-end Markets, end-users of A/B type.
1. Bag size is 210 mm (width) * 310 mm (length). Material is OPP or multi-layer PP.
2. Front must have clear window to show packed products. Back clear window is optional.
3. Front side must have logo that stands out (Willow Crest) as attached.
4. Front side must have product name and net weight.
5. Back side must have enough space for Nutrition Fact, product descriptions (110 mm * 100 mm), and barcode.
6. Back side must have white space to print production and expiry dates about 25 mm * 30 mm.
7. Top and bottom of bag must be opaque and not show product.
Reason: Extended period for more new ideas and also for requested modification.
Target Market(s)
Premium market. Type A to B customers as well as professional clients. The product is not a snack. It is for cooking or baking.
Industry/Entity Type
Food Store
Requirements
Must have
- Look unique and stand out from others in the market.
- The colors of the word "Willow Crest" and the blue air-brush in the logo can be changed.
Nice to have
- See project description
Should not have
- See project description

```html
<!DOCTYPE html>
<html lang="en">
<head>
<meta charset="utf-8">
<title>Willow Crest – Retail Bag Range</title>
<link href="https://fonts.googleapis.com/css2?family=Bebas+Neue&family=Montserrat:wght@800&display=swap" rel="stylesheet">
<style>
  :root {
    --stage: #f1f1f2;
    --bag-base: #eceef0;
    --bag-light: #f7f7f8;
    --pumpkin: #e8922a;
    --almond: #5a8ccd;
    --ink: #111111;
    --brand-blue: #2d4a9e;
    --label-white: #ffffff;
    --badge-text: #8a6a3a;
    --seed-light: #efe3c4;
    --seed-mid: #d9c79c;
    --nut-light: #c9844a;
    --nut-dark: #8a4a22;
  }
  * { box-sizing: border-box; margin: 0; padding: 0; }
  html, body { width: 1200px; height: 1200px; overflow: hidden; }
  body { background: var(--stage); position: relative; font-family: "Bebas Neue", sans-serif; }

  .bag {
    position: absolute;
    top: 258px;
    width: 411px;
    height: 602px;
    overflow: hidden;
    background:
      conic-gradient(from 180deg at 50% 100%, transparent 0deg, rgba(255,255,255,.35) 8deg, transparent 16deg, rgba(255,255,255,.3) 28deg, transparent 38deg, rgba(255,255,255,.3) 322deg, transparent 334deg, rgba(255,255,255,.35) 344deg, transparent 352deg),
      linear-gradient(180deg, var(--accent) 0%, color-mix(in srgb, var(--accent) 45%, var(--bag-light)) 35%, var(--bag-base) 60%, var(--bag-light) 100%);
  }
  .bag--pumpkin { left: 99px; --accent: var(--pumpkin); }
  .bag--almond { left: 663px; --accent: var(--almond); }

  .brand-panel {
    position: absolute;
    left: 97px; top: 0;
    width: 216px; height: 192px;
    background: var(--label-white);
    opacity: .94;
    display: flex; align-items: center; justify-content: center; gap: 10px;
  }
  .brand-mark { width: 22px; height: 22px; border-radius: 50%; background: var(--brand-blue); }
  .brand-name { font-size: 38px; color: var(--brand-blue); letter-spacing: 1px; }

  .product-line {
    position: absolute; left: 0; right: 0; top: 224px;
    text-align: center; font-size: 24px; letter-spacing: 7px; color: var(--ink);
  }
  .product-name {
    position: absolute; left: 0; right: 0; top: 244px;
    text-align: center; font-size: 116px; line-height: 1; color: var(--ink); letter-spacing: -1px;
  }
  .product-sub {
    position: absolute; left: 0; right: 0; top: 340px;
    text-align: center; font-size: 58px; line-height: 1; color: var(--ink);
  }

  .window {
    position: absolute; left: 61px; top: 434px;
    width: 300px; height: 200px;
    border-radius: 150px 150px 0 0;
  }
  .window--seeds { background: radial-gradient(circle at 50% 40%, var(--seed-light), var(--seed-mid)); }
  .window--nuts { left: 56px; width: 300px; background: radial-gradient(circle at 50% 40%, var(--nut-light), var(--nut-dark)); }

  .badge {
    position: absolute; top: 510px;
    width: 72px; height: 72px; border-radius: 50%;
    background: var(--label-white);
    display: flex; align-items: center; justify-content: center;
    font-family: "Montserrat", sans-serif; font-weight: 800;
    font-size: 16px; line-height: .95; text-align: center; color: var(--badge-text);
  }
  .badge--1 { left: 82px; }
  .badge--2 { left: 170px; }
  .badge--3 { left: 254px; }
</style>
</head>
<body>
  <section class="bag bag--pumpkin">
    <div class="brand-panel"><span class="brand-mark"></span><span class="brand-name">Willow Crest</span></div>
    <p class="product-line">Premium Organic</p>
    <h1 class="product-name">Pumpkin</h1>
    <p class="product-sub">Seeds</p>
    <div class="window window--seeds" role="img" aria-label="Clear window showing shelled pumpkin seeds"></div>
    <span class="badge badge--1">HEA<br>LTHY</span>
    <span class="badge badge--2">NAT<br>URAL</span>
    <span class="badge badge--3">ORG<br>ANIC</span>
  </section>

  <section class="bag bag--almond">
    <div class="brand-panel"><span class="brand-mark"></span><span class="brand-name">Willow Crest</span></div>
    <p class="product-line">Premium Organic</p>
    <h1 class="product-name">Almonds</h1>
    <div class="window window--nuts" role="img" aria-label="Clear window showing whole almonds"></div>
    <span class="badge badge--1">HEA<br>LTHY</span>
    <span class="badge badge--2">NAT<br>URAL</span>
    <span class="badge badge--3">ORG<br>ANIC</span>
  </section>
</body>
</html>
```